Redesign of business card for Cedar Ridge Mechanical

We are looking for a new design for our business cards for Cedar Ridge Mechanical. We are a plumbing & HVAC construction company, operating on the West Coast of Canada and USA. Logo attached.
Industry/Entity Type
Construction - Plumbing & HVAC
Contact Information for Business Card
Name, address, phone numbers, email, website address
Look and feel
Each slider illustrates characteristics of the customer's brand and the style your logo design should communicate.

```html
<!DOCTYPE html>
<html lang="en">
<head>
<meta charset="UTF-8">
<title>Cedar Ridge Mechanical – Business Card</title>
<link href="https://fonts.googleapis.com/css2?family=Montserrat:wght@400;700&display=swap" rel="stylesheet">
<style>
  :root {
    --page: #2b2d31;
    --card-white: #ffffff;
    --card-black: #111213;
    --ink: #1a1a1a;
    --ink-soft: #3a3a3a;
    --swoosh: #8a8a8a;
    --back-text: #d9d9d9;
  }
  * { box-sizing: border-box; margin: 0; padding: 0; }
  html, body { width: 1200px; height: 900px; overflow: hidden; }
  body {
    background: var(--page);
    font-family: "Montserrat", sans-serif;
    display: flex;
    flex-direction: column;
    align-items: center;
    justify-content: center;
    gap: 60px;
  }
  .card {
    position: relative;
    width: 560px;
    height: 320px;
    border-radius: 22px;
    overflow: hidden;
    box-shadow: 0 14px 30px rgba(0,0,0,.35);
  }
  /* Front */
  .card--front { background: var(--card-white); color: var(--ink); }
  .front-band { position: absolute; inset: 0; width: 100%; height: 100%; }
  .front-band .band { fill: var(--card-black); }
  .front-band .swoosh { fill: var(--swoosh); }
  .front-content {
    position: absolute;
    top: 44px; left: 40px; right: 30px;
    display: flex;
    align-items: flex-start;
  }
  .brand {
    width: 200px;
    display: flex;
    align-items: center;
    gap: 10px;
    padding-top: 30px;
  }
  .brand-mark {
    width: 16px; height: 16px;
    background: var(--ink);
    flex: none;
  }
  .brand-name {
    font-weight: 700;
    font-size: 15px;
    line-height: 1.25;
    text-transform: uppercase;
    letter-spacing: .04em;
    color: var(--ink);
  }
  .divider {
    width: 1.5px;
    height: 170px;
    background: var(--ink);
    margin: 0 22px 0 14px;
    flex: none;
  }
  .contact { padding-top: 4px; }
  .contact-name { font-weight: 700; font-size: 22px; line-height: 1.1; }
  .contact-role { font-size: 12.5px; color: var(--ink-soft); margin-top: 2px; }
  .contact-address { font-size: 12.5px; color: var(--ink-soft); margin-top: 8px; line-height: 1.35; }
  .contact-list { list-style: none; margin-top: 10px; }
  .contact-list li {
    display: flex; align-items: center; gap: 8px;
    font-size: 12.5px; color: var(--ink-soft); line-height: 1.7;
  }
  .contact-list svg { width: 11px; height: 11px; fill: var(--ink); flex: none; }
  /* Back */
  .card--back {
    background: var(--card-black);
    display: flex; align-items: center; justify-content: center;
  }
  .back-brand { display: flex; align-items: center; gap: 14px; }
  .back-brand .brand-mark { width: 22px; height: 22px; background: var(--back-text); }
  .back-brand .brand-name { font-size: 26px; color: var(--back-text); }
</style>
</head>
<body>

<section class="card card--front" aria-label="Business card front">
  <svg class="front-band" viewBox="0 0 560 320" preserveAspectRatio="none" aria-hidden="true">
    <path class="band" d="M0 232 C 170 268, 390 270, 560 236 L560 320 L0 320 Z"/>
    <path class="swoosh" d="M40 214 C 200 250, 390 252, 540 222 C 390 246, 200 246, 40 214 Z"/>
  </svg>
  <div class="front-content">
    <div class="brand">
      <span class="brand-mark"></span>
      <span class="brand-name">Cedar Ridge Mechanical</span>
    </div>
    <div class="divider"></div>
    <div class="contact">
      <p class="contact-name">Daniel Hayes</p>
      <p class="contact-role">Managing Director</p>
      <p class="contact-address">240 Harbor View Road<br>Bellingham, WA 98225</p>
      <ul class="contact-list">
        <li><svg viewBox="0 0 24 24"><path d="M6.6 10.8a15.1 15.1 0 0 0 6.6 6.6l2.2-2.2c.3-.3.7-.4 1-.2 1.1.4 2.3.6 3.6.6.6 0 1 .4 1 1V20c0 .6-.4 1-1 1A17 17 0 0 1 3 4c0-.6.4-1 1-1h3.5c.6 0 1 .4 1 1 0 1.3.2 2.5.6 3.6.1.3 0 .7-.2 1z"/></svg>888.555.0142</li>
        <li><svg viewBox="0 0 24 24"><path d="M2 5h20v14H2z M2 5l10 8 10-8" /></svg>info@cedarridgemech.com</li>
        <li><svg viewBox="0 0 24 24"><circle cx="12" cy="12" r="10"/></svg>www.cedarridgemech.com</li>
      </ul>
    </div>
  </div>
</section>

<section class="card card--back" aria-label="Business card back">
  <div class="back-brand">
    <span class="brand-mark"></span>
    <span class="brand-name">Cedar Ridge Mechanical</span>
  </div>
</section>

</body>
</html>
```